Launching a new real estate agency in Monaco

Hello, I am opening a new real estate agency in Monaco. For the purpose of my activity, in order to be known quickly among a fierce competition I need an advertising campaign that will be broadcast in local magazines, newspapers, paper board, etc.

You will find example of pictures of Monaco on which I have the rights and my logo. You can always pick other images that I can buy if the price is reasonable for a commercial use (<200 $)

Please respect the color code.

I wish you good luck and look forward to give you my feedbacks

Reason: Only few projects posted were respecting the brief and of quality. Hoping to receive more in coming days

Target Market(s)

International high-end clientele of all ages, all genders.

Industry/Entity Type

Real Estate Agent

Font styles to use
Serif

Requirements
Must have
• 1/ My logo
• 2/ This message "Un nouveau regard sur l'immobilier" means in English a fresh look at real estate or new eyes on real-estate.
• 3/ My address: 14 rue des Ormeaux, Galerie Bellerive Nord, 98 000 Monaco
• 4/ Phone number: +377.93.48.25.07
• 5/ Website: www.corvano-immo.com.
• 6/ Format: Files should be easily adjustable but I'd like a vertical display to fit easily in Magazines, Poster and billboard. So please work in high resolution !
Nice to have
• Please think about your design in accordance with the message I want to display.
Should not have
• A simple poster with a picture of Monaco that does not take into consideration the message of the advertisement, "Un nouveau regard sur l'immobilier" which means in english, new eyes on real-estate or a new look at real-estate, or new vision at real-estate.

```html
<!DOCTYPE html>
<html lang="fr">
<head>
<meta charset="utf-8">
<title>Corvano Immo – Un nouveau regard sur l'immobilier</title>
<link rel="stylesheet" href="https://fonts.googleapis.com/css2?family=Bodoni+Moda:opsz,wght@6..96,800&family=Arimo:wght@400;700&display=swap">
<style>
  :root {
    --navy: #18283f;
    --blush: #e8b1a2;
    --white: #ffffff;
    --backdrop: #e4e4e4;
    --lens-light: #6f87a3;
    --lens-dark: #3e5573;
  }
  * { margin: 0; padding: 0; box-sizing: border-box; }
  html, body { width: 1200px; height: 1200px; overflow: hidden; }
  body { background: var(--backdrop); position: relative; }

  .poster {
    position: absolute;
    left: 226px; top: 40px;
    width: 748px; height: 1120px;
    background: var(--navy);
    overflow: hidden;
  }
  .poster__website {
    position: absolute;
    right: 38px; top: 62px;
    font: 400 16.5px/1 "Arimo", sans-serif;
    color: var(--white);
  }
  .poster__view {
    position: absolute;
    left: 0; top: 0;
    width: 748px; height: 1120px;
  }
  .headline-band {
    position: absolute;
    left: 0; top: 568px;
    width: 100%; height: 355px;
    background: var(--blush);
    display: flex; align-items: center; justify-content: center;
  }
  .headline {
    font: 800 82px/99px "Bodoni Moda", serif;
    color: var(--navy);
    text-align: center;
    text-transform: uppercase;
    letter-spacing: 0.5px;
  }
  .footer {
    position: absolute;
    left: 0; top: 923px;
    width: 100%; height: 197px;
  }
  .brand {
    position: absolute;
    left: 50px; top: 78px;
    display: flex; align-items: center; gap: 10px;
  }
  .brand__mark {
    width: 22px; height: 22px;
    background: var(--blush);
  }
  .brand__name {
    font: 800 24px/1 "Bodoni Moda", serif;
    color: var(--blush);
    letter-spacing: 1.5px;
    white-space: nowrap;
  }
  .footer__divider {
    position: absolute;
    left: 372px; top: 43px;
    width: 4px; height: 104px;
    background: var(--blush);
  }
  .contact {
    position: absolute;
    left: 406px; top: 52px;
    width: 330px;
    color: var(--blush);
  }
  .contact__phone {
    font: 700 33px/1 "Arimo", sans-serif;
    letter-spacing: 0.5px;
  }
  .contact__address {
    margin-top: 14px;
    font: 400 16px/21px "Arimo", sans-serif;
  }
</style>
</head>
<body>
  <main class="poster">
    <p class="poster__website">www.corvano-immo.com</p>

    <svg class="poster__view" viewBox="0 0 693 1037" role="img" aria-label="Photograph of the Monaco harbour and the Rock seen through a binocular-shaped frame">
      <defs>
        <linearGradient id="lens-fill" x1="0" y1="0" x2="0" y2="1">
          <stop offset="0" stop-color="var(--lens-light)"/>
          <stop offset="1" stop-color="var(--lens-dark)"/>
        </linearGradient>
      </defs>
      <g fill="url(#lens-fill)">
        <ellipse cx="221" cy="315" rx="195" ry="159"/>
        <ellipse cx="471" cy="315" rx="195" ry="159"/>
      </g>
    </svg>

    <section class="headline-band">
      <h1 class="headline">Un nouveau<br>regard sur<br>l'immobilier</h1>
    </section>

    <footer class="footer">
      <div class="brand">
        <span class="brand__mark"></span>
        <span class="brand__name">CORVANO IMMO</span>
      </div>
      <span class="footer__divider"></span>
      <div class="contact">
        <p class="contact__phone">+377.93.48.25.07</p>
        <p class="contact__address">14 rue des Ormeaux, Galerie Bellerive Nord, 98 000 Monaco</p>
      </div>
    </footer>
  </main>
</body>
</html>
```